PSD Website Design

I am looking to have a custom website designed. I would like a PSD made of the design I came up with. Once I get the design I will slice the PSD and create a wordpress template from it.

See attachment for basic layout of the graphic. The image labeled Player page is the basic page I will need for the website. I also need a home page with an image slider on it and thumbnails of recent, state video uploads.

A textured background is ok.

Looking for a quick turnaround.

Text at top of page is a menu that is needed. Open to seeing the menu as a navigational bar or/and with different font types.

No preference on page background color or font colors. I welcome creativity.

```html
<!DOCTYPE html>
<html lang="en">
<head>
<meta charset="utf-8">
<title>Summit Athletic Recruiting – Player Profile</title>
<link href="https://fonts.googleapis.com/css2?family=Oswald:wght@400;500&family=Open+Sans:wght@400;600;700&family=Cabin:wght@400;500;700&display=swap" rel="stylesheet">
<style>
:root{
  --orange:#e8730c;
  --orange-dark:#c85f06;
  --red:#d62f2c;
  --red-dark:#a81f1d;
  --page-bg:#e4e5e8;
  --white:#ffffff;
  --ink:#2b2b2b;
  --grey-text:#666;
  --nav-text:#6b6b6b;
  --link-blue:#2a5db0;
  --ad-grey:#c3c3c3;
  --footer-bg:#3b3b3b;
  --footer-dark:#1e1e1e;
  --panel-dark:#2a2a2a;
  --sky:#6fcbef;
  --input-bg:#8e8e8e;
}
*{box-sizing:border-box;margin:0;padding:0}
html,body{width:843px;height:1200px;overflow:hidden}
body{position:relative;background:var(--page-bg);font-family:"Open Sans",sans-serif;color:var(--ink)}
.abs{position:absolute}

/* header */
.site-header{position:absolute;left:0;top:0;width:843px;height:64px;background:var(--white);border-bottom:6px solid var(--orange)}
.brand{left:80px;top:14px}
.brand-name{font-family:"Cabin",sans-serif;font-weight:700;font-size:29px;line-height:28px;color:var(--ink);display:flex;align-items:center;gap:6px}
.brand-name .dot{width:12px;height:12px;background:var(--orange);display:inline-block}
.brand-tag{font-family:"Cabin",sans-serif;font-weight:700;font-size:8px;letter-spacing:2.2px;color:var(--ink);margin-top:3px}
.main-nav{left:319px;top:29px;display:flex;gap:0;font-family:"Cabin",sans-serif;font-size:14.5px;color:var(--nav-text)}
.main-nav a{text-decoration:none;color:inherit;margin-right:22px;position:relative}
.main-nav a.active{color:var(--orange)}
.main-nav a.active::after{content:"";position:absolute;left:50%;top:25px;margin-left:-5px;border:5px solid transparent;border-bottom-color:var(--orange)}
.search{left:653px;top:28px;width:102px;height:22px;border:1px solid #c9c9c9;border-radius:3px;background:#f0f0f0;display:flex}
.search span{flex:1;font-size:9.5px;font-style:italic;color:#999;padding:5px 8px}
.search i{width:24px;border-left:1px solid #c9c9c9;background:#e2e2e2;display:flex;align-items:center;justify-content:center}

/* content panel */
.content{left:74px;top:78px;width:686px;height:912px;background:var(--white)}

.photo-frame{left:86px;top:100px;width:178px;height:214px;background:var(--white);box-shadow:0 2px 6px rgba(0,0,0,.35);transform:rotate(-2deg);padding:8px}
.photo-frame .photo{width:100%;height:100%;background:linear-gradient(160deg,#d6e6b4,#b9d08f)}
.photo-back{left:92px;top:104px;width:178px;height:214px;background:var(--white);box-shadow:0 1px 4px rgba(0,0,0,.25)}
.player-name{left:278px;top:99px;font-family:"Open Sans",sans-serif;font-weight:600;font-size:19px;color:var(--ink)}
.player-pos{left:278px;top:125px;font-size:10px;font-weight:600;color:var(--link-blue)}
.player-stats{left:278px;top:140px;font-size:9px;line-height:14.6px;color:#333}
.player-stats li{list-style:none}
.class-of{left:275px;top:283px;font-family:"Oswald",sans-serif;font-size:11px;letter-spacing:.6px;color:#7a9a25}

/* tab banners */
.tab-banner{height:52px}
.tab-banner svg{position:absolute;left:0;top:0}
.tab-banner .label{position:absolute;left:0;right:0;top:8px;text-align:center;font-family:"Oswald",sans-serif;font-size:17px;color:var(--white);letter-spacing:-.2px}

.film-grid{left:460px;top:150px;width:290px}
.video-card{position:absolute;width:93px}
.thumb{width:93px;height:52px;position:relative}
.thumb .dur{position:absolute;right:2px;bottom:2px;background:rgba(0,0,0,.8);color:#fff;font-size:5.5px;padding:0 2px}
.video-card h4{font-weight:400;font-size:6.6px;line-height:8px;color:var(--link-blue);margin-top:4px}
.video-card p{font-size:5.2px;line-height:7px;color:#777}
.channel-row{left:460px;top:258px;width:290px;border-top:1px solid #e3e3e3;padding-top:6px;font-size:5.5px;color:#999;display:flex;align-items:center;gap:4px}
.channel-row b{font-size:7.5px;color:#333}
.channel-row i{width:9px;height:9px;border-radius:50%;background:#333;display:inline-block}

.section-heading{font-family:"Oswald",sans-serif;font-size:17px;color:var(--orange);display:flex;align-items:center;gap:5px}
.section-heading::before,.section-heading::after{content:"";height:2px;background:var(--orange)}
.highlights-heading{left:86px;top:373px;width:390px}
.highlights-heading::before{width:20px}.highlights-heading::after{flex:1;background:linear-gradient(90deg,var(--orange),#fff)}
.viral-heading{left:490px;top:687px;width:265px}
.viral-heading::before{width:18px}.viral-heading::after{flex:1;background:linear-gradient(90deg,var(--orange),#fff)}

.player{background:#000}
.player .screen{position:absolute;left:0;top:0;right:0;bottom:22px}
.player .bar{position:absolute;left:0;right:0;bottom:0;height:22px;background:linear-gradient(#2a2a2a,#111);display:flex;align-items:center;padding:0 10px;gap:10px;color:#bbb;font-size:6px}
.player .progress{position:absolute;left:0;right:0;bottom:22px;height:3px;background:#444}
.player .progress b{display:block;height:100%;background:#c11}
.highlight-video{left:87px;top:405px;width:382px;height:236px;box-shadow:0 6px 10px rgba(0,0,0,.18)}
.recruits-video{left:88px;top:732px;width:382px;height:234px}

.ad-spot{left:535px;top:405px;width:211px;height:211px;background:var(--ad-grey);display:flex;align-items:center;justify-content:center;font-family:"Oswald",sans-serif;font-size:20px;color:var(--white)}

.viral-box{left:498px;top:732px;width:249px;height:235px;background:var(--panel-dark);border-radius:2px}
.event-card{left:510px;top:746px;width:223px;height:94px;background:var(--white);border-radius:2px;padding:4px 6px}
.event-card h3{font-family:"Oswald",sans-serif;font-weight:500;font-size:17px;color:#111;line-height:22px}
.event-card p{font-size:10.2px;line-height:14.8px;color:#111}
.connect-band{left:483px;top:853px;width:251px;height:27px;background:var(--sky);font-family:"Oswald",sans-serif;font-size:16px;color:var(--white);padding:1px 0 0 30px}
.connect-fold{left:483px;top:880px}
.social-list{left:512px;top:898px;display:flex;gap:14px}
.social-list span{width:44px;height:44px;border-radius:6px;box-shadow:0 3px 0 #2ba9d9;display:block}

/* footer */
.site-footer{left:0;top:990px;width:843px;height:182px;background:var(--footer-bg);border-top:4px solid var(--orange)}
.foot-title{font-family:"Oswald",sans-serif;font-size:17px;color:var(--orange)}
.foot-links{left:98px;top:1047px;list-style:none;font-size:12.5px;line-height:21.5px;color:#fff}
.contact-list{left:273px;top:1045px;list-style:none;font-size:12.5px;color:#fff}
.contact-list li{display:flex;gap:8px;align-items:flex-start;margin-bottom:10px;line-height:15px}
.field{background:var(--input-bg);border:1px solid #aaa;color:#eee;font-size:11.5px;font-style:italic;padding:2px 6px}
.send-btn{left:690px;top:1135px;width:60px;height:21px;background:var(--orange);color:#fff;font-size:12px;text-align:center;line-height:21px}
.copyright{left:0;top:1172px;width:843px;height:28px;background:var(--footer-dark);color:#eee;font-size:11px;padding:6px 82px}
</style>
</head>
<body>

<header class="site-header">
  <div class="abs brand">
    <div class="brand-name"><span class="dot"></span>SUMMIT</div>
    <div class="brand-tag">ATHLETIC RECRUITING</div>
  </div>
  <nav class="abs main-nav">
    <a href="#">Home</a><a href="#">About us</a><a href="#">State</a><a href="#" class="active">Position</a><a href="#">Join</a>
  </nav>
  <div class="abs search"><span>search here...</span><i>
    <svg width="12" height="12" viewBox="0 0 12 12"><circle cx="5" cy="5" r="3.5" fill="none" stroke="#666" stroke-width="1.6"/><line x1="7.5" y1="7.5" x2="11" y2="11" stroke="#666" stroke-width="2"/></svg></i></div>
</header>

<main>
  <div class="abs content"></div>

  <!-- player profile -->
  <div class="abs photo-back"></div>
  <div class="abs photo-frame"><div class="photo" role="img" aria-label="Player portrait photo"></div></div>
  <h1 class="abs player-name">Marcus Dalton</h1>
  <div class="abs player-pos">Wide Receiver</div>
  <ul class="abs player-stats">
    <li>Miami, FL (Bayview Central)</li>
    <li>Ht: 6-1.5 &nbsp;|&nbsp; Wt: 197</li>
    <li>40 Time: 4.45</li>
    <li>Bench: 22 Reps</li>
    <li>Vertical: 36</li>
    <li>5-10-5 Shuttle: 4.42</li>
  </ul>
  <div class="abs class-of">CLASS OF 2015</div>

  <!-- game film -->
  <div class="abs tab-banner" style="left:457px;top:86px;width:291px">
    <svg width="291" height="60" viewBox="0 0 291 60">
      <line x1="0" y1="24" x2="291" y2="24" stroke="#555" stroke-width="3"/>
      <path d="M58 24 L72 2 H220 L234 24 Z" fill="var(--red-dark)"/>
      <path d="M78 4 H214 L200 40 Q196 52 180 52 H112 Q96 52 92 40 Z" fill="var(--red)" stroke="#fff" stroke-width="3"/>
    </svg>
    <div class="label">GAME FILM</div>
  </div>

  <div class="abs film-grid">
    <div class="video-card" style="left:0;top:0"><div class="thumb" role="img" aria-label="Video thumbnail" style="background:linear-gradient(#6b8f5a,#4d6b3c)"><span class="dur">9:56</span></div><h4>Spring combine route drills and footwork</h4><p>by fieldcam 10,820 views<br>3 years ago</p></div>
    <div class="video-card" style="left:98px;top:0"><div class="thumb" role="img" aria-label="Video thumbnail" style="background:linear-gradient(#7d8d5e,#585e48)"><span class="dur">7:54</span></div><h4>Seven on seven camp</h4><p>by coachreel 10,358 views 3 years ago</p></div>
    <div class="video-card" style="left:196px;top:0"><div class="thumb" role="img" aria-label="Video thumbnail" style="background:linear-gradient(#8a8f88,#4f5a48)"><span class="dur">6:23</span></div><h4>Summer passing league highlights reel part two</h4><p>by gridfilm 32,118 views<br>4 years ago</p></div>
  </div>
  <div class="abs channel-row"><i></i><b>gridfilm</b> Popular channel this week - we think you'll like it</div>
  <div class="abs film-grid" style="top:273px">
    <div class="video-card" style="left:0;top:0"><div class="thumb" role="img" aria-label="Video thumbnail" style="background:linear-gradient(#2a8ed8,#c83a2a)"><span class="dur">23:45</span></div><h4>Red zone scrimmage full game replay</h4><p>by gridfilm 17,498 views<br>1 year ago</p></div>
    <div class="video-card" style="left:98px;top:0"><div class="thumb" role="img" aria-label="Video thumbnail" style="background:linear-gradient(#b59a7a,#7a6450)"><span class="dur">4:47</span></div><h4>Defensive back drills with coach Ray</h4><p>by gridfilm 4,842 views<br>2 years ago</p></div>
    <div class="video-card" style="left:196px;top:0"><div class="thumb" role="img" aria-label="Video thumbnail" style="background:linear-gradient(#3aa0d8,#3a8a3a)"><span class="dur">13:33</span></div><h4>Spring showcase mashup and top plays</h4><p>by gridfilm 10,769 views<br>2 years ago</p></div>
  </div>

  <!-- highlights -->
  <h2 class="abs section-heading highlights-heading">HIGHLIGHTS</h2>
  <div class="abs player highlight-video">
    <div class="screen" role="img" aria-label="Highlight video of a team gathered on an indoor field" style="background:linear-gradient(#d9d6d2 0%,#9a8f8a 35%,#6d2a34 65%,#2a2a2e 100%)"></div>
    <div class="progress"><b style="width:4%"></b></div>
    <div class="bar"><span>▶</span><span>◀)</span><span>0:12 / 7:50</span></div>
  </div>

  <div class="abs ad-spot">ADVERTISEMENT SPOT</div>

  <!-- recent recruits -->
  <div class="abs tab-banner" style="left:86px;top:672px;width:384px">
    <svg width="384" height="60" viewBox="0 0 384 60">
      <line x1="0" y1="26" x2="384" y2="26" stroke="#555" stroke-width="3"/>
      <path d="M104 26 L118 2 H266 L280 26 Z" fill="var(--red-dark)"/>
      <path d="M124 4 H260 L246 40 Q242 52 226 52 H158 Q142 52 138 40 Z" fill="var(--red)" stroke="#fff" stroke-width="3"/>
    </svg>
    <div class="label">RECENT RECRUITS</div>
  </div>
  <div class="abs player recruits-video">
    <div class="screen">
      <svg class="abs" style="left:181px;top:98px" width="20" height="20" viewBox="0 0 20 20">
        <g fill="#888"><circle cx="10" cy="3" r="2"/><circle cx="17" cy="10" r="2" opacity=".5"/><circle cx="10" cy="17" r="2" opacity=".7"/><circle cx="3" cy="10" r="2" opacity=".9"/></g>
      </svg>
    </div>
    <div class="progress" style="background:#333"><b style="width:1%"></b></div>
    <div class="bar"><span>▶</span><span>◀)</span><span>0:00 / 1:36</span></div>
  </div>

  <!-- take it viral -->
  <h2 class="abs section-heading viral-heading">TAKE IT VIRAL</h2>
  <div class="abs viral-box"></div>
  <div class="abs event-card">
    <h3>NEXT EVENT</h3>
    <p>Lorem ipsum dolor sit amet,consectetuer adipiscing elit, sed diam nonummy nibh euismod tincidunt ut laoreet dolore magna aliquam erat volutpat.</p>
  </div>
  <div class="abs connect-band">CONNECT WITH GRIDLINE</div>
  <svg class="abs connect-fold" width="16" height="14" viewBox="0 0 16 14"><path d="M0 0 H16 V14 Z" fill="#3b9fc4"/></svg>
  <div class="abs social-list">
    <span style="background:#3b5a9a"></span>
    <span style="background:#3cb6e6"></span>
    <span style="background:#d8d8d8"></span>
    <span style="background:#9a7a5a"></span>
  </div>
</main>

<footer class="abs site-footer"></footer>
<h3 class="abs foot-title" style="left:100px;top:1009px">QUICK LINKS</h3>
<div class="abs" style="left:80px;top:1039px;width:140px;height:1px;background:#555"></div>
<ul class="abs foot-links"><li>About us</li><li>Position</li><li>State</li><li>Join</li></ul>

<h3 class="abs foot-title" style="left:290px;top:1009px">CONTACT US</h3>
<div class="abs" style="left:270px;top:1039px;width:160px;height:1px;background:#555"></div>
<ul class="abs contact-list">
  <li><svg width="12" height="14" viewBox="0 0 12 14"><path d="M6 0a5 5 0 0 1 5 5c0 4-5 9-5 9S1 9 1 5a5 5 0 0 1 5-5z" fill="#aaa"/><circle cx="6" cy="5" r="2" fill="#3b3b3b"/></svg><span>Address: 234 Street Name,<br>City, State 12345</span></li>
  <li><svg width="12" height="14" viewBox="0 0 12 14"><path d="M2 1 L5 1 L6 4 L4 5.5 Q5.5 9 8 10 L9.5 8 L12 9 L12 12 Q6 13 2 8 Q0 4 2 1z" fill="#aaa"/></svg><span>1234-5677-8901</span></li>
  <li><svg width="14" height="14" viewBox="0 0 14 14"><rect x="1" y="3" width="12" height="9" fill="none" stroke="#aaa"/><path d="M1 3 L7 8 L13 3" fill="none" stroke="#aaa"/></svg><span>contact@email.com</span></li>
</ul>

<h3 class="abs foot-title" style="left:538px;top:1009px">GET IN TOUCH</h3>
<div class="abs field" style="left:539px;top:1044px;width:92px;height:20px">Name</div>
<div class="abs field" style="left:644px;top:1044px;width:107px;height:20px">Email</div>
<div class="abs field" style="left:539px;top:1072px;width:211px;height:56px;padding-top:5px">Your Message...</div>
<div class="abs send-btn">Send</div>

<div class="abs copyright">© 2014 Summit Athletic Recruiting, All Rights Reserved</div>

</body>
</html>
```